Jewelers Website

This is for the DESIGN ONLY.
I am a software programmer and will be doing the development.
New website design for
www.lunacrestgems.com.au
Need a fresh new look for an online only jewellery business who produce their jewellery by hand. I would like it designed in a parallax style. Feel free to recommend fonts to use for the site. This is an Australian based company located in NSW so shots of sites in NSW might make nice background images.
http://vornaplex.me/demo/#theme=parallax
To contain the below sections
About Us
Contact Us
Gallery
Testimonials
Diamond Types
The colour scheme is to be Black / White and Silver.
With the Parallax style there will be moving sections and images for added impact.
Target Market(s)
Young Adults mainly engagement jewellery

```html
<!DOCTYPE html>
<html lang="en">
<head>
<meta charset="utf-8">
<title>Lunacrest Gems — Diamond Engagement Rings &amp; Jewellery</title>
<link rel="stylesheet" href="https://fonts.googleapis.com/css2?family=Cinzel:wght@400;700&family=Crimson+Text:ital,wght@0,400;0,600;1,400&family=Jost:wght@400;500&display=swap">
<style>
  :root {
    --ink: #1a1a1a;
    --bar: #2a2a2a;
    --black: #050505;
    --white: #ffffff;
    --silver: #c9c9c9;
    --silver-light: #e6e6e6;
    --grey-text: #8a8a8a;
    --grey-sub: #6a6a6a;
    --field-line: #d6d6d6;
  }
  * { box-sizing: border-box; margin: 0; padding: 0; }
  html, body { width: 1200px; height: 2500px; overflow: hidden; background: var(--white); }
  body { position: relative; font-family: "Crimson Text", Georgia, serif; color: var(--ink); }
  .abs { position: absolute; }

  /* Header */
  .site-header { position: absolute; left: 0; top: 0; width: 1200px; height: 87px; background: var(--bar); }
  .brand { position: absolute; left: 140px; top: 12px; font-family: "Cinzel", Georgia, serif; font-weight: 400; color: var(--white); font-size: 30px; line-height: 30px; letter-spacing: 0.5px; }
  .main-nav { position: absolute; left: 432px; top: 36px; display: flex; gap: 30px; }
  .main-nav a, .footer-nav a { font-family: "Jost", Arial, sans-serif; color: var(--white); text-decoration: none; font-size: 14px; letter-spacing: 0.3px; }

  /* Hero */
  .hero { position: absolute; left: 0; top: 87px; width: 1200px; height: 436px; background: radial-gradient(ellipse at 45% 45%, #f0f0f0 0%, #b8b8b8 45%, #d9d9d9 75%, #ececec 100%); }
  .hero-title { position: absolute; left: 788px; top: 108px; font-family: "Cinzel", Georgia, serif; color: var(--ink); font-size: 40px; line-height: 42px; }
  .hero-title span { display: block; font-size: 34px; }
  .slide-dots { position: absolute; left: 1149px; top: 125px; display: flex; flex-direction: column; gap: 17px; }
  .slide-dots i { width: 12px; height: 12px; border-radius: 50%; background: #a8a8a8; }
  .slide-dots i.active { background: var(--white); }

  .notch { position: absolute; left: 573px; width: 54px; height: 27px; background: var(--black); }
  .notch.up { top: 496px; border-radius: 27px 27px 0 0; }
  .notch.down { top: 928px; border-radius: 0 0 27px 27px; }

  /* About */
  .about { position: absolute; left: 0; top: 523px; width: 1200px; height: 405px; background: var(--black); }
  .about-photo { position: absolute; right: 0; top: 0; width: 420px; height: 405px; background: radial-gradient(ellipse at 55% 45%, #6a5040 0%, #2e2118 45%, #050505 85%); }
  .about h2 { position: absolute; left: 215px; top: 105px; font-family: "Cinzel", Georgia, serif; font-weight: 400; font-size: 44px; color: var(--grey-text); }
  .about h3 { position: absolute; left: 215px; top: 160px; font-weight: 400; font-size: 25px; color: var(--grey-sub); }
  .about p { position: absolute; left: 215px; top: 200px; width: 450px; font-size: 14px; line-height: 19px; color: #d8d8d8; }
  .btn-light { position: absolute; font-family: "Crimson Text", Georgia, serif; font-weight: 600; font-size: 13px; letter-spacing: 0.5px; color: var(--ink); background: linear-gradient(#f4f4f4, #cfcfcf); border-radius: 4px; display: flex; align-items: center; justify-content: center; }
  .about .btn-light { left: 215px; top: 274px; width: 105px; height: 34px; }

  /* Testimonials */
  .testimonials { position: absolute; left: 0; top: 928px; width: 1200px; height: 544px; background: linear-gradient(90deg, #d9cfc8 0%, #efeae6 30%, #f4f2f0 55%, #d6d1cc 80%, #bfb8b2 100%); }
  .testimonials-top { position: absolute; left: 0; top: 0; width: 1200px; height: 240px; background: rgba(255,255,255,0.55); }
  .testimonials h2 { position: absolute; left: 0; top: 52px; width: 1200px; text-align: center; font-family: "Cinzel", Georgia, serif; font-weight: 400; font-size: 33px; color: #444; }
  .testimonials h2 b { color: var(--ink); font-weight: 400; }
  .testimonials .intro { position: absolute; left: 205px; top: 118px; width: 790px; text-align: center; font-size: 15px; line-height: 19px; color: var(--ink); }
  .testimonials .btn-light { left: 548px; top: 197px; width: 103px; height: 33px; }
  .reviews { position: absolute; left: 0; top: 240px; width: 1200px; height: 304px; background: rgba(255,255,255,0.25); }
  .review { position: absolute; top: 0; width: 290px; text-align: center; }
  .review .avatar { width: 146px; height: 146px; margin: 25px auto 0; border-radius: 50%; border: 3px solid rgba(255,255,255,0.8); background: radial-gradient(circle at 50% 40%, #e2c3a8 0%, #a07a5e 60%, #5a4334 100%); }
  .review h4 { margin-top: 14px; font-weight: 600; font-size: 14px; letter-spacing: 0.6px; }
  .review p { margin-top: 6px; font-size: 14px; line-height: 17px; padding: 0 8px; }

  /* Gallery + diamond types */
  .showcase { position: absolute; left: 0; top: 1472px; width: 1200px; height: 565px; background: radial-gradient(ellipse at 30% 40%, #3a3a3a 0%, #141414 50%, #050505 100%); }
  .showcase h2 { position: absolute; left: 0; width: 1200px; text-align: center; font-family: "Cinzel", Georgia, serif; font-weight: 700; font-size: 32px; color: var(--white); }
  .gallery-item { position: absolute; top: 110px; width: 232px; height: 150px; }
  .arrow { position: absolute; width: 24px; height: 44px; }
  .type { position: absolute; top: 356px; width: 110px; text-align: center; }
  .type .disc { width: 110px; height: 110px; border-radius: 50%; background: #2f2f2f; display: flex; align-items: center; justify-content: center; }
  .type span { display: block; margin-top: 10px; font-style: italic; font-size: 17px; color: var(--white); }

  /* Contact */
  .contact { position: absolute; left: 0; top: 2037px; width: 1200px; height: 363px; background: var(--white); }
  .contact-photo { position: absolute; left: 40px; top: 60px; width: 420px; height: 260px; background: radial-gradient(ellipse at 45% 55%, #e2e2e2 0%, #f2f2f2 45%, #ffffff 75%); }
  .contact h2 { position: absolute; left: 258px; top: 50px; font-family: "Cinzel", Georgia, serif; font-weight: 700; font-size: 32px; color: var(--ink); }
  .field { position: absolute; border: 2px solid var(--field-line); border-radius: 4px; background: rgba(255,255,255,0.6); font-size: 13px; color: #888; padding: 10px 12px; }
  .submit { position: absolute; left: 860px; top: 261px; width: 115px; height: 42px; background: var(--bar); color: var(--white); border-radius: 5px; font-family: "Crimson Text", Georgia, serif; font-weight: 600; font-size: 20px; letter-spacing: 0.5px; display: flex; align-items: center; justify-content: center; }

  /* Footer */
  .site-footer { position: absolute; left: 0; top: 2400px; width: 1200px; height: 100px; background: var(--bar); }
  .footer-nav { position: absolute; left: 137px; top: 34px; display: flex; gap: 25px; }
  .footer-nav a { font-size: 12px; }
  .social { position: absolute; left: 765px; top: 30px; display: flex; gap: 26px; font-family: "Crimson Text", Georgia, serif; font-weight: 600; font-size: 15px; color: var(--white); }
  .copyright { position: absolute; left: 812px; top: 70px; font-family: "Jost", Arial, sans-serif; font-size: 12px; color: var(--silver); }
</style>
</head>
<body>

<header class="site-header">
  <div class="brand">LUNACREST<br>GEMS</div>
  <nav class="main-nav">
    <a href="#">HOME</a><a href="#">ABOUT US</a><a href="#">CONTACT US</a><a href="#">GALLERY</a><a href="#">TESTIMONIALS</a><a href="#">DIAMOND TYPES</a>
  </nav>
</header>

<section class="hero" role="img" aria-label="Close-up photograph of a diamond engagement ring resting on a wedding band, in silver grey tones">
  <h1 class="hero-title">LUNACREST<span>GEMS</span></h1>
  <div class="slide-dots"><i class="active"></i><i></i><i></i><i></i></div>
</section>

<div class="notch up">
  <svg width="54" height="27" viewBox="0 0 54 27"><path d="M21 20 L27 14 L33 20" fill="none" stroke="#fff" stroke-width="2"/></svg>
</div>

<section class="about">
  <div class="about-photo" role="img" aria-label="Photograph of a couple holding hands, showing an engagement ring, in warm dark tones"></div>
  <h2>ABOUT US</h2>
  <h3>Diamond Engagement Rings &amp; Jewellery</h3>
  <p>At Lunacrest Gems we specialise in creating beautiful jewellery and diamond engagement rings using the very best diamonds, gemstones and precious metals from Australia and around the world.</p>
  <div class="btn-light">READ MORE</div>
</section>

<div class="notch down">
  <svg width="54" height="27" viewBox="0 0 54 27"><path d="M21 8 L27 14 L33 8" fill="none" stroke="#fff" stroke-width="2"/></svg>
</div>

<section class="testimonials" role="img" aria-label="Soft photograph of a smiling engaged couple outdoors, used as section background">
  <div class="testimonials-top"></div>
  <h2>STORIES &amp; <b>TESTIMONIALS</b></h2>
  <p class="intro">Lorem ipsum dolor sit amet, consectetur adipisicing elit, sed do eiusmod tempor incididunt ut labore et dolore magna aliqua. Ut enim ad minim veniam, quis nostrud exercitation ullamco laboris nisi ut aliquip ex ea commodo consequat. Duis aute irure dolor in reprehenderit in voluptate velit esse</p>
  <div class="btn-light">STORIES</div>
  <div class="reviews">
    <div class="review" style="left:160px">
      <div class="avatar" role="img" aria-label="Portrait photo of Angelica"></div>
      <h4>ANGELICA</h4>
      <p>Lorem ipsum dolor sit amet, consectetur adipisicing elit, sed do eiusmod tempor incididunt ut labore et dolore</p>
    </div>
    <div class="review" style="left:450px">
      <div class="avatar" role="img" aria-label="Portrait photo of Jully"></div>
      <h4>JULLY</h4>
      <p>Lorem ipsum dolor sit amet, consectetur adipisicing elit, sed do eiusmod tempor incididunt ut labore et dolore</p>
    </div>
    <div class="review" style="left:752px">
      <div class="avatar" role="img" aria-label="Portrait photo of Jessi"></div>
      <h4>JESSI</h4>
      <p>Lorem ipsum dolor sit amet, consectetur adipisicing elit, sed do eiusmod tempor incididunt ut labore et dolore</p>
    </div>
  </div>
</section>

<section class="showcase" role="img" aria-label="Dark background of scattered loose diamonds">
  <h2 style="top:40px">GALLERY</h2>
  <svg class="arrow" style="left:51px;top:148px" viewBox="0 0 24 44"><path d="M22 2 L2 22 L22 42" fill="none" stroke="#ccc" stroke-width="2"/></svg>
  <div class="gallery-item" style="left:107px;background:linear-gradient(135deg,#f2f2f2,#9a9a9a 60%,#d8d8d8)" role="img" aria-label="Photo of loose cut diamonds"></div>
  <div class="gallery-item" style="left:358px;background:linear-gradient(135deg,#c94a55,#e8e2dc 45%,#f4f2ee)" role="img" aria-label="Photo of a ring beside a red flower"></div>
  <div class="gallery-item" style="left:610px;background:radial-gradient(circle,#f4efd8,#c9a45c 55%,#7d6235)" role="img" aria-label="Photo of a gold halo diamond ring"></div>
  <div class="gallery-item" style="left:862px;background:radial-gradient(circle,#a08a6e,#e8e6e2 55%,#f6f6f6)" role="img" aria-label="Photo of a gold and diamond cocktail ring"></div>
  <svg class="arrow" style="left:1126px;top:148px" viewBox="0 0 24 44"><path d="M2 2 L22 22 L2 42" fill="none" stroke="#ccc" stroke-width="2"/></svg>

  <h2 style="top:290px">DIAMOND TYPES</h2>
  <svg class="arrow" style="left:51px;top:389px" viewBox="0 0 24 44"><path d="M22 2 L2 22 L22 42" fill="none" stroke="#ccc" stroke-width="2"/></svg>
  <div class="type" style="left:170px">
    <div class="disc"><svg width="60" height="60" viewBox="0 0 60 60"><circle cx="30" cy="30" r="26" fill="#e8e8e8" stroke="#999"/><polygon points="30,12 48,30 30,48 12,30" fill="none" stroke="#999"/></svg></div><span>Round</span>
  </div>
  <div class="type" style="left:352px">
    <div class="disc"><svg width="60" height="60" viewBox="0 0 60 60"><rect x="6" y="6" width="48" height="48" fill="#e0e0e0" stroke="#999"/><rect x="18" y="18" width="24" height="24" fill="none" stroke="#999"/></svg></div><span>Princes</span>
  </div>
  <div class="type" style="left:533px">
    <div class="disc"><svg width="60" height="60" viewBox="0 0 60 60"><path d="M30 4 Q50 30 30 56 Q10 30 30 4Z" fill="#e8e8e8" stroke="#999"/><line x1="30" y1="4" x2="30" y2="56" stroke="#999"/></svg></div><span>Marquise</span>
  </div>
  <div class="type" style="left:727px">
    <div class="disc"><svg width="60" height="60" viewBox="0 0 60 60"><path d="M30 4 Q52 32 46 44 Q30 62 14 44 Q8 32 30 4Z" fill="#e8e8e8" stroke="#999"/><polygon points="30,18 40,38 20,38" fill="none" stroke="#999"/></svg></div><span>Pear</span>
  </div>
  <div class="type" style="left:920px">
    <div class="disc"><svg width="60" height="60" viewBox="0 0 60 60"><polygon points="16,4 44,4 52,12 52,48 44,56 16,56 8,48 8,12" fill="#e8e8e8" stroke="#999"/><rect x="20" y="16" width="20" height="28" fill="none" stroke="#999"/></svg></div><span>Radiant</span>
  </div>
  <svg class="arrow" style="left:1126px;top:389px" viewBox="0 0 24 44"><path d="M2 2 L22 22 L2 42" fill="none" stroke="#ccc" stroke-width="2"/></svg>
</section>

<section class="contact">
  <div class="contact-photo" role="img" aria-label="Soft-focus photo of a solitaire diamond ring on white"></div>
  <h2>CONTACT</h2>
  <div class="field" style="left:262px;top:110px;width:230px;height:46px">Name</div>
  <div class="field" style="left:503px;top:110px;width:230px;height:46px">Phone Number</div>
  <div class="field" style="left:745px;top:110px;width:230px;height:46px">Email Id</div>
  <div class="field" style="left:262px;top:175px;width:713px;height:76px">Message</div>
  <div class="submit">SUBMIT</div>
</section>

<footer class="site-footer">
  <nav class="footer-nav">
    <a href="#">HOME</a><a href="#">ABOUT US</a><a href="#">CONTACT US</a><a href="#">GALLERY</a><a href="#">TESTIMONIALS</a><a href="#">DIAMOND TYPES</a>
  </nav>
  <div class="social"><span>Friendly</span><span>Chirp</span><span>Vidline</span><span>Picgram</span></div>
  <div class="copyright">© 2014.www.companyname.com</div>
</footer>

</body>
</html>
```